Business cards and stationary design

We just completed the design of our new logo and we need to print new business cards and letterhead for our nonprofit. We are looking for a fresh new design that shows off our new logo. On letterhead, we must have a column on the right or left to include our Board of Directors (up to 45 names) (see attachment)

Industry/Entity Type

Non-Profit

Contact Information for Business Card

Standard business card with name, title, Company name, mailing address phone numbers, email address and website. Tagline on back "Bringing the homeless home"

Font styles to use
Sans Serif

Requirements
Must have
• include pertinent information above
• new logo
• fonts compatible with logo
• should use logo colors only
Nice to have
• tag lines

```html
<!DOCTYPE html>
<html lang="en">
<head>
<meta charset="utf-8">
<title>Homeward Haven – Business Card</title>
<link href="https://fonts.googleapis.com/css2?family=Jura:wght@400;500;600&display=swap" rel="stylesheet">
<style>
  :root {
    --backdrop: #d8d5cf;
    --card-face: #eef0f1;
    --card-edge: #ffffff;
    --teal: #1d5a72;
    --teal-deep: #164a60;
    --orange: #e89a2a;
    --name-ink: #dfe4e6;
    --detail-ink: #d6dde0;
    --link-ink: #cfc6a4;
    --brand-ink: #1f5b73;
  }
  html, body {
    margin: 0;
    width: 1200px;
    height: 969px;
    overflow: hidden;
    background: var(--backdrop);
  }
  .business-card {
    position: absolute;
    left: 100px;
    top: 199px;
    width: 1000px;
    height: 571px;
    background: var(--card-face);
    border: 2px solid var(--card-edge);
    box-sizing: border-box;
    overflow: hidden;
    box-shadow: 0 18px 40px rgba(0,0,0,0.18);
    font-family: "Jura", sans-serif;
  }
  .card-shapes {
    position: absolute;
    inset: 0;
  }
  .brand-name {
    position: absolute;
    left: 60px;
    top: 160px;
    width: 420px;
    text-align: center;
    font-size: 38px;
    font-weight: 600;
    letter-spacing: 3px;
    color: var(--brand-ink);
  }
  .holder {
    position: absolute;
    right: 52px;
    top: 238px;
    text-align: right;
  }
  .holder-name {
    font-size: 36px;
    font-weight: 600;
    letter-spacing: 3px;
    color: var(--name-ink);
    line-height: 1;
  }
  .holder-title {
    margin-top: 10px;
    font-size: 22px;
    font-weight: 500;
    letter-spacing: 2px;
    color: var(--name-ink);
  }
  .mailing-address {
    position: absolute;
    right: 52px;
    top: 322px;
    text-align: right;
    font-size: 22px;
    line-height: 29px;
    color: var(--detail-ink);
  }
  .contact-list {
    position: absolute;
    right: 52px;
    top: 424px;
    margin: 0;
    padding: 0;
    list-style: none;
    text-align: right;
  }
  .contact-list li {
    display: flex;
    justify-content: flex-end;
    align-items: center;
    gap: 12px;
    height: 32px;
    font-size: 20px;
    color: var(--link-ink);
  }
  .contact-list li.phone {
    font-size: 23px;
    color: var(--detail-ink);
    height: 36px;
  }
  .contact-icon {
    width: 20px;
    height: 20px;
    fill: var(--detail-ink);
  }
</style>
</head>
<body>
  <div class="business-card">
    <svg class="card-shapes" viewBox="0 0 1000 571" preserveAspectRatio="none" aria-hidden="true">
      <defs>
        <linearGradient id="tealPanel" x1="0" y1="0" x2="1" y2="1">
          <stop offset="0" stop-color="var(--teal)"/>
          <stop offset="1" stop-color="var(--teal-deep)"/>
        </linearGradient>
      </defs>
      <polygon class="teal-panel" points="0,545 979,90 1000,103 1000,571 0,571" fill="url(#tealPanel)"/>
      <polyline class="white-rule" points="0,539 979,84 1000,97" fill="none" stroke="#ffffff" stroke-width="3"/>
      <polyline class="orange-roofline" points="0,527 979,72 1000,85" fill="none" stroke="var(--orange)" stroke-width="13"/>
    </svg>

    <div class="brand-name">HOMEWARD HAVEN</div>

    <div class="holder">
      <div class="holder-name">DANIEL REYES</div>
      <div class="holder-title">CEO/FOUNDER</div>
    </div>

    <div class="mailing-address">
      Homeward Haven<br>
      2140 Birchwood Avenue<br>
      Juneau, Alaska 99801
    </div>

    <ul class="contact-list">
      <li class="phone">555 218 4096
        <svg class="contact-icon" viewBox="0 0 24 24"><path d="M6.6 10.8a15.1 15.1 0 0 0 6.6 6.6l2.2-2.2a1 1 0 0 1 1-.25 11.4 11.4 0 0 0 3.6.57 1 1 0 0 1 1 1V20a1 1 0 0 1-1 1A17 17 0 0 1 3 4a1 1 0 0 1 1-1h3.5a1 1 0 0 1 1 1c0 1.25.2 2.45.57 3.57a1 1 0 0 1-.25 1z"/></svg>
      </li>
      <li class="email">daniel@homewardhaven.org
        <svg class="contact-icon" viewBox="0 0 24 24"><path d="M3 5h18v14H3z M3 5l9 7 9-7" fill="var(--detail-ink)" stroke="var(--teal)" stroke-width="1.6"/></svg>
      </li>
      <li class="web">www.homewardhaven.org
        <svg class="contact-icon" viewBox="0 0 24 24"><circle cx="12" cy="12" r="10"/><path d="M2 12h20M12 2c3 3 3 17 0 20M12 2c-3 3-3 17 0 20" fill="none" stroke="var(--teal)" stroke-width="1.5"/></svg>
      </li>
    </ul>
  </div>
</body>
</html>
```